I have a logo and need to design the business card and stationery.
Updates

The uploaded logo image named as GREYMARSH CONSTRUCTION which is to be replaced to GREYMARSH CONTRACTS. Kindly add below details and submit the designs- Company name- Greymarsh Engineering Contracts LLP Name & Post- Kelvan Joshi (Designated Partner) Address- Block No.317, Wing C, Tulvo Trade Court, Manek Pural Road, Ruparel Industrial Estate, Goregaon(E), Mumbai - 400 063 Contact- +91 97415 60382 Email- kelvanjoshi@mailbrook.example Website- www.greymarshcontracts.example Contact for Letterhead- +91-22-28754193

Hi Tovin Rahul, We are liking your Design #28860835. We have suggested some changes which are mentioned in feedback. Kindly revert with it asap to finalize this design.

Colors

Designer to choose colors to be used in the design.

```html
<!DOCTYPE html>
<html lang="en">
<head>
<meta charset="utf-8">
<title>Greymarsh Contracts Letterhead</title>
<link href="https://fonts.googleapis.com/css2?family=Open+Sans:wght@400;700&family=Roboto:wght@400&display=swap" rel="stylesheet">
<style>
  :root {
    --backdrop: #dcdcdc;
    --paper: #f8f8f8;
    --ink: #4f4f4f;
    --brand: #3d3d3d;
    --band: #3e3e3e;
    --band-text: #f2f2f2;
    --signature-tone: #e6e6e6;
  }
  * { margin: 0; padding: 0; box-sizing: border-box; }
  html, body {
    width: 1153px; height: 1200px; overflow: hidden;
    background: var(--backdrop);
  }
  .letterhead {
    position: absolute; left: 168px; top: 30px;
    width: 817px; height: 1140px;
    background: var(--paper);
    font-family: "Open Sans", sans-serif;
    color: var(--ink);
  }
  .brand {
    position: absolute; top: 48px; left: 0; right: 0;
    display: flex; flex-direction: column; align-items: center; gap: 14px;
  }
  .brand-square {
    width: 62px; height: 62px; background: var(--brand);
  }
  .brand-name {
    font-family: "Open Sans", sans-serif;
    font-weight: 700; font-size: 24px; letter-spacing: 1px;
    color: var(--brand); line-height: 1;
  }
  .letter-body {
    position: absolute; left: 73px; top: 290px; width: 669px;
    font-size: 14.6px; line-height: 22px;
  }
  .salutation { margin-bottom: 22px; }
  .letter-body p.paragraph { text-align: justify; margin-bottom: 22px; }
  .signature {
    width: 100px; height: 92px; margin-top: 28px;
    background: var(--signature-tone);
  }
  .footer-band {
    position: absolute; left: 0; bottom: 0; width: 100%; height: 104px;
    background: var(--band); color: var(--band-text);
    font-family: "Roboto", sans-serif; font-size: 13px; line-height: 17px;
    display: flex; justify-content: space-between;
    padding: 26px 73px 0;
  }
  .contact-list { list-style: none; }
  .contact-list li { display: flex; align-items: center; gap: 4px; }
  .contact-list svg { width: 12px; height: 12px; fill: var(--band-text); }
  .company-address { text-align: right; font-style: normal; }
</style>
</head>
<body>
<div class="letterhead">
  <header class="brand">
    <div class="brand-square"></div>
    <div class="brand-name">GREYMARSH CONTRACTS</div>
  </header>

  <main class="letter-body">
    <p class="salutation">Dear customer,</p>
    <p class="paragraph">Lorem ipsum dolor sit amet, consectetur adipisicing elit, sed do eiusmod tempor incididunt ut labore et dolore magna aliqua. Ut enim ad minim veniam, quis nostrud exercitation ullamco laboris nisi ut aliquip ex ea commodo consequat. Duis aute irure dolor in reprehenderit in voluptate velit esse cillum dolore eu fugiat nulla pariatur. Excepteur sint occaecat cupidatat non proident, sunt in culpa qui officia deserunt mollit anim id est laborum.</p>
    <p class="paragraph">Lorem ipsum dolor sit amet, consectetur adipisicing elit, sed do eiusmod tempor incididunt ut labore et dolore magna aliqua. Ut enim ad minim veniam, quis nostrud exercitation ullamco laboris nisi ut aliquip ex ea commodo consequat. Duis aute irure dolor in reprehenderit in voluptate velit esse cillum dolore eu fugiat nulla pariatur. Excepteur sint occaecat cupidatat non proident, sunt in culpa qui officia deserunt mollit anim id est laborum.</p>
    <p class="paragraph">Lorem ipsum dolor sit amet, consectetur adipisicing elit, sed do eiusmod tempor incididunt ut labore et dolore magna aliqua. Ut enim ad minim veniam, quis nostrud exercitation ullamco laboris nisi ut aliquip ex ea commodo consequat. Duis aute irure dolor in reprehenderit in voluptate velit esse cillum dolore eu fugiat nulla pariatur. Excepteur sint occaecat cupidatat non proident, sunt in culpa qui officia deserunt mollit anim id est laborum.</p>
    <p class="paragraph">Lorem ipsum dolor sit amet, consectetur adipisicing elit, sed do eiusmod tempor incididunt ut labore et dolore magna aliqua. Ut enim ad minim veniam, quis nostrud exercitation ullamco laboris nisi ut aliquip ex ea commodo consequat. Duis aute irure dolor in reprehenderit.</p>
    <p class="closing">Yours Sincerely,</p>
    <div class="signature" role="img" aria-label="Handwritten signature"></div>
  </main>

  <footer class="footer-band">
    <ul class="contact-list">
      <li>
        <svg viewBox="0 0 12 12"><path d="M1 4c0-2 2-3 5-3s5 1 5 3l-2 1-1-2H4L3 5 1 4zM3 6h6l1 5H2l1-5zm3 1.2a1.5 1.5 0 100 3 1.5 1.5 0 000-3z"/></svg>
        +91-22-28754193
      </li>
      <li>
        <svg viewBox="0 0 12 12"><path d="M1 2.5h10v7H1zM1.8 3.2 6 6.6l4.2-3.4v.9L6 7.5 1.8 4.1z" fill-rule="evenodd"/></svg>
        info@greymarshcontracts.example
      </li>
      <li>
        <svg viewBox="0 0 12 12"><circle cx="6" cy="6" r="5"/><path d="M3.5 3.5c1 0 1.5.5 1.5 1.5s-1 1-1 2 .8 1.5.5 2.5c-1-.6-2-1.6-2-3.5 0-1 .4-2 1-2.5zM7.5 2.5c.8.2 1.5 1 1 1.8-.6.6-1.5.2-1.3 1.2.2.8 1.4.6 1.6 1.7-.4 1-1 1.6-1.6 1.8.2-1 .6-1.5-.3-2.2C6 6 5.9 4.8 6.8 4c.5-.5.5-1 .7-1.5z" fill="#3e3e3e"/></svg>
        www.greymarshcontracts.example
      </li>
    </ul>
    <address class="company-address">
      Greymarsh Engineering Contracts LLP<br>
      Block No.317, Wing C, Tulvo Trade Court, Manek Pural Road,<br>
      Ruparel Industrial Estate, Goregaon(E), Mumbai - 400 063
    </address>
  </footer>
</div>
</body>
</html>
```